Fresh Dwelling Tract Guide needs a new Landing Page

I like to get a landing page or website with 2-3 pages to help target home buyers who are looking to buy homes from builders such as TW Residences, Morvik, P.L. Fennick, etc. The landing page/website to be non-cluttered and be able to explain to home buyers that there are many benefits to include me as their buyer's agent when they buy a brand new home from any builders.
I may want to incorporate a short explanation video (animated) on the landing page and then for the viewer to click on a button that will take them to another page where they can search for new homes from different builders.
Target Market(s)
Home buyers looking to buy brand new home from builders such as TW Residences, Morvik, P.L. Fennick, etc.
Industry/Entity Type
Real Estate
Number of Pages Required
2 page
Font styles to use
Requirements
Must have
- The landing page may have the explanation video at the bottom of the landing page (scrolled down) or there may be a CALL TO ACTION button that takes the viewer to the 2nd page to watch the explanation video. Once they watched the explanation video and are still interested, they can click on another CALL TO ACTION button that will take them to another website that they will be able to search for all the available new homes and register their contact information.
Should not have
- No clutters and no dark colors.

```html
<!DOCTYPE html>
<html lang="en">
<head>
<meta charset="utf-8">
<title>Fresh Dwelling Tract Guide</title>
<link rel="stylesheet" href="https://fonts.googleapis.com/css2?family=Poppins:wght@300;500;600;700&family=Raleway:wght@400;500&family=Roboto:wght@700&display=swap">
<style>
  :root {
    --brand-red: #c41a20;
    --footer-red: #d2454a;
    --white: #ffffff;
    --hero-light: #d9d9d7;
    --hero-mid: #a9a6a2;
    --hero-warm: #8a7a68;
  }
  * { box-sizing: border-box; margin: 0; padding: 0; }
  html, body { width: 1200px; height: 1086px; overflow: hidden; }
  body { position: relative; font-family: "Raleway", sans-serif; color: var(--white); background: var(--white); }

  .hero { position: absolute; left: 0; top: 0; width: 1200px; height: 669px; overflow: hidden; }
  .hero-photo {
    position: absolute; inset: 0;
    background:
      radial-gradient(ellipse at 50% 30%, rgba(255,255,255,0.25), transparent 60%),
      linear-gradient(180deg, var(--hero-light) 0%, #c4c2bf 45%, var(--hero-mid) 75%, var(--hero-warm) 100%);
  }
  .hero-shade { position: absolute; inset: 0; background: rgba(60,60,60,0.28); }

  .site-header { position: absolute; left: 95px; top: 15px; display: flex; align-items: center; gap: 14px; }
  .brand-dot { width: 64px; height: 64px; border-radius: 50%; background: var(--white); }
  .brand-name { font-family: "Poppins", sans-serif; font-weight: 600; font-size: 31px; letter-spacing: -0.2px; }
  .menu-toggle { position: absolute; left: 1033px; top: 47px; width: 20px; height: 17px; }

  .hero-copy { position: absolute; left: 0; top: 240px; width: 1200px; text-align: center; }
  .hero-kicker { font-family: "Poppins", sans-serif; font-weight: 300; font-size: 50px; line-height: 60px; }
  .hero-title { font-family: "Poppins", sans-serif; font-weight: 600; font-size: 66px; line-height: 76px; letter-spacing: -0.5px; }
  .watch-video { display: inline-flex; align-items: center; gap: 12px; font-family: "Raleway", sans-serif; font-weight: 500; font-size: 28px; line-height: 34px; margin-top: 14px; }
  .cta {
    position: absolute; left: 455px; top: 450px; width: 290px; height: 66px;
    border-radius: 33px; background: var(--brand-red);
    box-shadow: 0 4px 10px rgba(0,0,0,0.25);
    font-family: "Roboto", sans-serif; font-weight: 700; font-size: 17px; letter-spacing: 0.2px;
    display: flex; align-items: center; justify-content: center; color: var(--white); text-decoration: none;
  }
  .slider-dots { position: absolute; left: 563px; top: 626px; display: flex; gap: 11px; align-items: center; }
  .slider-dots span { width: 9px; height: 9px; border-radius: 50%; background: var(--white); }
  .slider-dots .active { width: 18px; height: 18px; background: transparent; border: 2px solid var(--white); position: relative; margin-right: -2px; }
  .slider-dots .active::after { content: ""; position: absolute; left: 3px; top: 3px; width: 8px; height: 8px; border-radius: 50%; background: var(--white); }

  .site-footer { position: absolute; left: 0; top: 669px; width: 1200px; height: 417px; overflow: hidden; text-align: center; }
  .footer-photo { position: absolute; inset: 0; background: linear-gradient(180deg, #d84a4e 0%, #cf4247 50%, #d8565a 100%); }
  .footer-inner { position: absolute; inset: 0; }
  .footer-mark { position: absolute; left: 561px; top: 36px; width: 78px; height: 78px; border-radius: 50%; background: var(--white); }
  .footer-title { position: absolute; left: 0; top: 133px; width: 1200px; font-family: "Poppins", sans-serif; font-weight: 600; font-size: 45px; line-height: 1.2; letter-spacing: -0.3px; }
  .contact-list { position: absolute; left: 0; top: 211px; width: 1200px; display: flex; justify-content: center; gap: 38px; list-style: none; font-size: 17px; }
  .contact-list li { display: flex; align-items: center; gap: 9px; }
  .social-list { position: absolute; left: 466px; top: 260px; display: flex; gap: 12px; list-style: none; }
  .social-list a {
    width: 44px; height: 44px; border-radius: 50%; background: var(--white);
    display: flex; align-items: center; justify-content: center;
    font-family: "Poppins", sans-serif; font-weight: 600; font-size: 10px;
    color: var(--brand-red); text-decoration: none;
  }
  .footer-nav { position: absolute; left: 0; top: 332px; width: 1200px; font-size: 17px; font-weight: 500; }
  .footer-nav a { color: var(--white); text-decoration: none; }
  .footer-nav .sep { margin: 0 11px; }
  .copyright { position: absolute; left: 0; top: 383px; width: 1200px; font-family: "Poppins", sans-serif; font-weight: 500; font-size: 13px; letter-spacing: 0.3px; }
</style>
</head>
<body>
  <section class="hero">
    <div class="hero-photo" role="img" aria-label="Bright open-plan dining room and living area in a new home"></div>
    <div class="hero-shade"></div>

    <header class="site-header">
      <span class="brand-dot"></span>
      <span class="brand-name">Fresh Dwelling Tract</span>
    </header>
    <svg class="menu-toggle" viewBox="0 0 20 17" aria-label="Menu">
      <rect y="0" width="20" height="3" rx="1" fill="#fff"/>
      <rect y="7" width="20" height="3" rx="1" fill="#fff"/>
      <rect y="14" width="20" height="3" rx="1" fill="#fff"/>
    </svg>

    <div class="hero-copy">
      <p class="hero-kicker">Welcome to</p>
      <h1 class="hero-title">Fresh Dwelling Tract</h1>
      <p class="watch-video">
        <svg width="28" height="28" viewBox="0 0 26 26" aria-hidden="true">
          <circle cx="13" cy="13" r="13" fill="#fff"/>
          <path d="M10 7.5 L19 13 L10 18.5 Z" fill="#8a8a8a"/>
        </svg>
        Watch Video
      </p>
    </div>
    <a class="cta" href="#">FIND YOUR DREAM HOUSE</a>
    <div class="slider-dots"><span class="active"></span><span></span><span></span><span></span></div>
  </section>

  <footer class="site-footer">
    <div class="footer-photo" role="img" aria-label="Lounge with large windows overlooking autumn trees, tinted red"></div>
    <div class="footer-inner">
      <span class="footer-mark"></span>
      <h2 class="footer-title">Fresh Dwelling Tract Guide</h2>
      <ul class="contact-list">
        <li>
          <svg width="17" height="17" viewBox="0 0 17 17" aria-hidden="true"><path d="M16 1 L1 7.5 L8 9 L9.5 16 Z" fill="#fff"/></svg>
          82 Larkspur Avenue Brookvale
        </li>
        <li>
          <svg width="14" height="14" viewBox="0 0 14 14" aria-hidden="true"><path d="M3 1 L5.5 1 L6.5 4 L5 5.5 C6 7.5 7 8.5 8.5 9 L10 7.5 L13 8.5 L13 11 C13 12.5 12 13 11 13 C5.5 12.5 1.5 8.5 1 3 C1 2 1.5 1 3 1 Z" fill="#fff"/></svg>
          Phone: +(555) 014-2290
        </li>
        <li>
          <svg width="17" height="13" viewBox="0 0 17 13" aria-hidden="true"><rect width="17" height="13" rx="1.5" fill="#fff"/><path d="M1 1.5 L8.5 7.5 L16 1.5" stroke="#d2454a" stroke-width="1.6" fill="none"/></svg>
          Email: hello@freshdwellingtract.com
        </li>
      </ul>
      <ul class="social-list" aria-label="Social links">
        <li><a href="#" aria-label="Loop">Loop</a></li>
        <li><a href="#" aria-label="Kivo">Kivo</a></li>
        <li><a href="#" aria-label="Frame">Frame</a></li>
        <li><a href="#" aria-label="Mesh">Mesh</a></li>
        <li><a href="#" aria-label="Orbi">Orbi</a></li>
      </ul>
      <nav class="footer-nav">
        <a href="#">Home</a><span class="sep">|</span><a href="#">About</a><span class="sep">|</span><a href="#">Our Services</a><span class="sep">|</span><a href="#">Our Blog</a><span class="sep">|</span><a href="#">Testimonials</a><span class="sep">|</span><a href="#">Contact us</a>
      </nav>
      <p class="copyright">Copyright © 2018. All Rights Reserved.</p>
    </div>
  </footer>
</body>
</html>
```